Basic business card

use my newly created logo - and the phrases (Lower Cost of Test & Accelarated New Product Introduction) - and my new email domain / ID - use at conferences / tradeshows

Industry/Entity Type

semiconductor

Contact Information for Business Card

Daniel K Forde, Owner, communicate via Logo - Lower COT - Cost of Test, Accelerated NPI - New Product Introduction, phone +1 555 613 0946, Chandler, Arizona, USA, daniel.forde@qal-vub.com

Font styles to use
Sans Serif

Requirements
Nice to have
• re-use my logo created via Pixel Harbor last August (#7315926)

```html
<!DOCTYPE html>
<html lang="en">
<head>
<meta charset="utf-8">
<title>QAL-VUB Business Card</title>
<link href="https://fonts.googleapis.com/css2?family=Open+Sans:wght@400;700&display=swap" rel="stylesheet">
<style>
  :root {
    --backdrop: #222222;
    --card: #151515;
    --slate: #4d5d7e;
    --orange: #f7941d;
    --cyan: #33bde9;
    --white: #f2f2f2;
  }
  * { margin: 0; padding: 0; box-sizing: border-box; }
  html, body {
    width: 1200px; height: 780px; overflow: hidden;
    background: var(--backdrop);
    font-family: "Open Sans", Arial, sans-serif;
  }
  .stage {
    width: 1200px; height: 780px;
    display: flex; align-items: center; justify-content: center; gap: 40px;
  }
  .card {
    width: 540px; height: 309px;
    background: var(--card);
    position: relative;
    box-shadow: 0 12px 30px rgba(0,0,0,0.55);
  }
  .brand {
    display: flex; align-items: center;
    color: var(--slate); font-weight: 400;
  }
  .brand-mark { background: var(--slate); flex: none; }
  .card-front .brand {
    position: absolute; inset: 0; justify-content: center; gap: 20px;
    font-size: 78px; letter-spacing: 2px;
  }
  .card-front .brand-mark { width: 44px; height: 44px; }
  .card-back .brand {
    position: absolute; left: 34px; top: 178px; gap: 10px;
    font-size: 36px; letter-spacing: 1px;
  }
  .card-back .brand-mark { width: 22px; height: 22px; }
  .divider {
    position: absolute; left: 272px; top: 58px;
    width: 1px; height: 190px; background: var(--cyan);
  }
  .contact { position: absolute; left: 292px; top: 60px; color: var(--white); }
  .contact-name { font-size: 24px; font-weight: 700; line-height: 1.1; }
  .first-name { color: var(--orange); }
  .last-name { color: var(--cyan); }
  .contact-role { font-size: 13px; margin-top: 2px; }
  .contact-list { list-style: none; margin-top: 20px; font-size: 13px; line-height: 1.6; }
  .contact-list li { display: flex; align-items: center; gap: 8px; }
  .contact-list svg { width: 12px; height: 12px; fill: var(--cyan); flex: none; }
  .contact-address { margin-top: 22px; font-size: 13px; line-height: 1.5; }
</style>
</head>
<body>
<main class="stage">
  <section class="card card-front">
    <div class="brand"><span class="brand-mark"></span><span class="brand-name">QAL-VUB</span></div>
  </section>

  <section class="card card-back">
    <div class="brand"><span class="brand-mark"></span><span class="brand-name">QAL-VUB</span></div>
    <div class="divider"></div>
    <div class="contact">
      <p class="contact-name"><span class="first-name">Nora</span> <span class="last-name">Vance</span></p>
      <p class="contact-role">Managing Director</p>
      <ul class="contact-list">
        <li><svg viewBox="0 0 24 24"><path d="M6.6 10.8a15 15 0 0 0 6.6 6.6l2.2-2.2c.3-.3.7-.4 1-.2 1.1.4 2.3.6 3.6.6.6 0 1 .4 1 1V20c0 .6-.4 1-1 1A17 17 0 0 1 3 4c0-.6.4-1 1-1h3.5c.6 0 1 .4 1 1 0 1.3.2 2.5.6 3.6.1.3 0 .7-.2 1z"/></svg>123 456 789</li>
        <li><svg viewBox="0 0 24 24"><path d="M2 5h20v14H2z M2 5l10 8 10-8" /></svg>info@samplemail.com</li>
        <li><svg viewBox="0 0 24 24"><circle cx="12" cy="12" r="10"/></svg>www.samplesite.com</li>
      </ul>
      <p class="contact-address">Your address, City<br>State, Zip 1234</p>
    </div>
  </section>
</main>
</body>
</html>
```